Seeking funky, innovative business cards

I am looking to refresh our current business cards to something more engaging, visual and impactful. We are a management consultancy firm, see website (www.larkstone-partners.com.au). I've included our colour scheme, sample of the slides we use and our old business cards. We would like our cards to have icons. The card should display:- Name- Title- Mobile number- Address- Email address- Website - Company logo- Our purpose statement "We shape bright places where teams thrive"

Contact Information for Business Card

Brennan Ulfsson
Consultant
0468 927 341
Suite 12, 218 Wexley Street, Ashvale 5071
brennan@larkstone-partners.com.au
www.larkstone-partners.com.au

Purpose statement "We shape bright places where teams thrive"
LOGO available in google images

Font styles to use
Other font styles liked:
• Open Sans Light, Bebas Neue (open to other cool foints)

Colors
ffc214
5c5c5c
f5f5f5
fefefe

Requirements
Must have
• - Name
• - Title
• - Mobile number
• - Address
• - Email address
• - Website
• - Company logo
• - Our purpose statement "We shape bright places where teams thrive"
Nice to have
• - Icons
• - Colour (see our colour scheme"

```html
<!DOCTYPE html>
<html lang="en">
<head>
<meta charset="utf-8">
<title>Larkstone Partners Australia – Business Card</title>
<link rel="stylesheet" href="https://fonts.googleapis.com/css2?family=Lato:wght@300;400;700&family=Roboto:wght@400&display=swap">
<style>
  :root {
    --backdrop: #d9d9d9;
    --card: #1d1e20;
    --card-edge: #242527;
    --accent: #ffc214;
    --text-light: #fefefe;
    --text-soft: #f5f5f5;
    --text-muted: #b9b9b9;
    --rule: #5c5c5c;
  }
  * { box-sizing: border-box; margin: 0; padding: 0; }
  html, body { width: 1200px; height: 1108px; overflow: hidden; }
  body {
    background: var(--backdrop);
    font-family: "Lato", sans-serif;
    position: relative;
  }
  .card {
    position: absolute;
    top: 204px;
    width: 440px;
    height: 700px;
    border-radius: 24px;
    background: var(--card);
    color: var(--text-light);
  }
  .card--front { left: 140px; text-align: center; }
  .card--back { left: 620px; background: var(--card-edge); overflow: hidden; }

  .brand { position: absolute; top: 150px; left: 0; right: 0; color: var(--text-light); font-weight: 300; }
  .brand__name { font-size: 78px; letter-spacing: -1px; line-height: 1; }
  .brand__sub { font-size: 15px; letter-spacing: 4px; margin-top: 6px; padding-left: 120px; }

  .person { position: absolute; top: 360px; left: 0; right: 0; }
  .person__name { color: var(--accent); font-size: 26px; font-weight: 400; letter-spacing: 0.5px; }
  .person__title { color: var(--text-muted); font-size: 18px; font-weight: 400; margin-top: 2px; }

  .icon-rule { position: absolute; top: 430px; left: 60px; right: 60px; height: 30px; display: flex; align-items: center; gap: 6px; }
  .icon-rule__line { flex: 1; height: 1px; background: var(--rule); }
  .icon-rule__icon { width: 28px; height: 28px; }

  .contact { position: absolute; top: 472px; left: 0; right: 0; font-size: 18px; line-height: 26px; color: var(--text-soft); }
  .divider { position: absolute; top: 566px; left: 80px; right: 80px; height: 1px; background: var(--rule); }
  .address { position: absolute; top: 580px; left: 0; right: 0; font-size: 19px; line-height: 27px; color: var(--text-soft); }

  .pattern-area {
    position: absolute; top: 0; left: 0; right: 0; height: 520px;
    background: radial-gradient(ellipse at 50% 30%, #2c2d30 0%, #26272a 55%, var(--card-edge) 100%);
  }
  .purpose {
    position: absolute; top: 560px; left: 0; right: 0; text-align: center;
    font-family: "Roboto", sans-serif; font-size: 22px; line-height: 30px;
    text-transform: uppercase; color: var(--text-light); letter-spacing: 0.3px;
  }
</style>
</head>
<body>
  <section class="card card--front" aria-label="Business card front">
    <div class="brand">
      <div class="brand__name">Larkstone</div>
      <div class="brand__sub">PARTNERS AUSTRALIA</div>
    </div>
    <div class="person">
      <div class="person__name">BRENNAN ULFSSON</div>
      <div class="person__title">Consultant</div>
    </div>
    <div class="icon-rule">
      <span class="icon-rule__line"></span>
      <svg class="icon-rule__icon" viewBox="0 0 28 28" aria-label="Phone">
        <circle cx="14" cy="14" r="14" fill="var(--accent)"/>
        <path d="M9 8.5c1-.8 2-.6 2.5.3l1 2c.3.6.1 1.2-.4 1.6l-.8.6c.7 1.6 1.9 2.8 3.5 3.5l.6-.8c.4-.5 1-.7 1.6-.4l2 1c.9.5 1.1 1.5.3 2.5-1 1.2-2.6 1.4-4.6.4-2.6-1.3-4.6-3.3-5.9-5.9-1-2-.8-3.6.4-4.6z" fill="#1d1e20"/>
      </svg>
      <svg class="icon-rule__icon" viewBox="0 0 28 28" aria-label="Email">
        <circle cx="14" cy="14" r="14" fill="var(--accent)"/>
        <rect x="7.5" y="9.5" width="13" height="9" rx="1" fill="#1d1e20"/>
        <path d="M8 10l6 4.5 6-4.5" stroke="var(--accent)" stroke-width="1.2" fill="none"/>
      </svg>
      <svg class="icon-rule__icon" viewBox="0 0 28 28" aria-label="Website">
        <circle cx="14" cy="14" r="14" fill="var(--accent)"/>
        <circle cx="14" cy="14" r="6.5" fill="none" stroke="#1d1e20" stroke-width="1.5"/>
        <ellipse cx="14" cy="14" rx="2.8" ry="6.5" fill="none" stroke="#1d1e20" stroke-width="1.2"/>
        <path d="M7.5 14h13" stroke="#1d1e20" stroke-width="1.2"/>
      </svg>
      <span class="icon-rule__line"></span>
    </div>
    <div class="contact">
      <div>0468 927 341</div>
      <div>brennan@larkstone-partners.com.au</div>
      <div>www.larkstone-partners.com.au</div>
    </div>
    <div class="divider"></div>
    <div class="address">
      <div>Suite 12, 218 Wexley</div>
      <div>Street, Ashvale 5071</div>
    </div>
  </section>

  <section class="card card--back" aria-label="Business card back">
    <div class="pattern-area" role="img" aria-label="Faint repeating network pattern of connected dots"></div>
    <p class="purpose">We shape bright places<br>where teams thrive</p>
  </section>
</body>
</html>
```